New Business Card Design Project

We require a business card design for Vexalund, a newly established Indian company.
Our focus is on the development, manufacturing, and export of a diverse array of pharmaceutical products on a global scale. The card should convey a professional appearance, as our primary markets are in Africa, China, and Southeast Asian nations.
We envision a two-sided business card, with the reverse side dedicated to a logo set against a solid color or an elegantly designed pattern. The corners should be rounded. We would appreciate seeing both horizontal and vertical design options. We trust the designer to utilize their expertise in creating this design.

The content for the business card is included in the attached Word file.

Target Market(s)

Our primary markets are in Africa, China, and Southeast Asian, Latin America, Maldives, Sri Lanka

Industry/Entity Type

Pharmaceutical Manufacturing and Export

Contact Information for Business Card

Colors

Designer to choose colors to be used in the design.

Requirements
Must have
• The reverse side of the business card features solely the logo along with the tagline, "Remedies of Life."
Should not have
• The logo should not exceed two instances, encompassing both the front and back sides of the card.

```html
<!DOCTYPE html>
<html lang="en">
<head>
<meta charset="utf-8">
<title>Vexalund Business Card</title>
<link href="https://fonts.googleapis.com/css2?family=Poppins:wght@400;600;700&display=swap" rel="stylesheet">
<style>
  :root {
    --brand-blue: #27a7df;
    --brand-red: #ef5c4b;
    --ink: #1f1f1f;
    --paper: #ffffff;
    --backdrop: #141414;
    --back-dark: #262626;
    --back-deep: #121212;
    --back-mid: #4a4a4a;
    --back-text: #bdbdbd;
  }
  * { margin: 0; padding: 0; box-sizing: border-box; }
  html, body {
    width: 1200px; height: 897px; overflow: hidden;
    background: var(--backdrop);
    font-family: "Poppins", sans-serif;
  }
  .canvas { position: relative; width: 1200px; height: 897px; }

  .card {
    position: absolute; left: 304px; width: 594px; height: 338px;
    border-radius: 22px; overflow: hidden;
  }
  .card--front { top: 92px; background: var(--paper); }
  .card--back { top: 470px; background: var(--back-dark); }

  .front__mark {
    position: absolute; left: 88px; top: 36px;
    width: 68px; height: 68px; border-radius: 50%;
    background: var(--brand-blue);
  }
  .front__brand {
    position: absolute; left: 29px; top: 124px;
    font-size: 38px; font-weight: 600; color: var(--brand-blue);
    line-height: 1; letter-spacing: 0.2px;
  }
  .front__person { position: absolute; right: 31px; top: 166px; text-align: right; }
  .person__name { font-size: 27px; font-weight: 700; line-height: 1; letter-spacing: 0.5px; }
  .person__first { color: var(--brand-blue); }
  .person__last { color: var(--brand-red); }
  .person__title { font-size: 15px; color: var(--ink); margin-top: 3px; line-height: 1.2; }

  .front__rule {
    position: absolute; left: 29px; right: 31px; top: 226px;
    height: 1px; background: var(--brand-blue);
  }
  .contact { position: absolute; left: 29px; top: 242px; list-style: none; }
  .contact__item {
    display: flex; align-items: center; gap: 4px;
    font-size: 15.5px; color: var(--ink); line-height: 19.5px;
  }
  .contact__icon { width: 11px; height: 11px; flex: none; }
  .contact__accent { color: var(--brand-red); }

  .address {
    position: absolute; right: 31px; top: 251px; text-align: right;
    font-size: 15.5px; color: var(--ink); line-height: 20px; font-style: normal;
  }
  .front__bands { position: absolute; left: 0; top: 0; }

  .back__pattern {
    position: absolute; inset: 0;
    background:
      radial-gradient(ellipse at 88% 15%, var(--back-mid) 0%, transparent 55%),
      linear-gradient(160deg, var(--back-dark) 0%, var(--back-deep) 60%, var(--back-deep) 100%);
  }
  .back__brand {
    position: absolute; left: 462px; top: 206px;
    display: flex; align-items: center; gap: 6px;
  }
  .back__dot { width: 10px; height: 10px; border-radius: 50%; background: var(--brand-red); flex: none; }
  .back__name { font-size: 18px; font-weight: 600; color: var(--brand-blue); line-height: 1; }
  .back__tagline {
    position: absolute; left: 462px; top: 232px; width: 110px;
    font-size: 11px; color: var(--back-text); line-height: 1; text-align: center;
  }
</style>
</head>
<body>
<main class="canvas">
  <section class="card card--front">
    <div class="front__mark"></div>
    <div class="front__brand">Vexalund</div>

    <div class="front__person">
      <div class="person__name"><span class="person__first">TOVA</span> <span class="person__last">MARSH</span></div>
      <div class="person__title">Founder &amp; Principal</div>
    </div>

    <div class="front__rule"></div>

    <ul class="contact">
      <li class="contact__item">
        <svg class="contact__icon" viewBox="0 0 12 12"><path d="M3 1 L5 3.5 L4 5 Q5.5 7.5 7 8 L8.5 7 L11 9 L9.5 11 Q4 10.5 1 3 Z" fill="none" stroke="var(--brand-blue)" stroke-width="1.1"/></svg>
        +1- 415-555-0148
      </li>
      <li class="contact__item">
        <svg class="contact__icon" viewBox="0 0 12 12"><rect x="1" y="2.5" width="10" height="7" fill="none" stroke="var(--brand-blue)" stroke-width="1.1"/><path d="M1 2.5 L6 6.5 L11 2.5" fill="none" stroke="var(--brand-blue)" stroke-width="1.1"/></svg>
        info@vexalund.com
      </li>
      <li class="contact__item">
        <svg class="contact__icon" viewBox="0 0 12 12"><circle cx="6" cy="6" r="5" fill="none" stroke="var(--brand-blue)" stroke-width="1.1"/><ellipse cx="6" cy="6" rx="2.2" ry="5" fill="none" stroke="var(--brand-blue)" stroke-width="0.9"/><path d="M1 6 H11" stroke="var(--brand-blue)" stroke-width="0.9"/></svg>
        <span>www.<span class="contact__accent">vexalund</span>.com</span>
      </li>
    </ul>

    <address class="address">
      4820 North 72nd Street<br>
      #18, Suite Riverside Park
    </address>

    <svg class="front__bands" width="594" height="338" viewBox="0 0 594 338">
      <path d="M0 318 H312 Q306 321 300 322 H0 Z" fill="var(--brand-red)"/>
      <path d="M0 326 H300 C330 326 345 313 375 313 H594 V338 H0 Z" fill="var(--brand-blue)"/>
    </svg>
  </section>

  <section class="card card--back">
    <div class="back__pattern" role="img" aria-label="Dark embossed repeating brand pattern across the whole back"></div>
    <div class="back__brand">
      <span class="back__dot"></span>
      <span class="back__name">Vexalund</span>
    </div>
    <div class="back__tagline">Remedies of Life</div>
  </section>
</main>
</body>
</html>
```